bluecrest mobile ultrasound business cards
Bluecrest Mobile Ultrasound
Bright & Fun-filled
Dana Whitcombe, RDMS, RVT
President/Owner
Hollywood, FL 33021
info@bluecrestmobileultrasound.example
www.bluecrestmobileultrasound.example

```html
<!DOCTYPE html>
<html lang="en">
<head>
<meta charset="utf-8">
<title>Bluecrest Mobile Ultrasound — Stationery</title>
<link href="https://fonts.googleapis.com/css2?family=Arimo:wght@400;700&family=Tinos:wght@700&display=swap" rel="stylesheet">
<style>
  :root {
    --bg: #2b2b2d;
    --paper: #ffffff;
    --ink: #3a3a3a;
    --muted: #8a8a8a;
    --rule: #bdbdbd;
    --orange: #f08a12;
    --orange-deep: #e9650c;
    --orange-light: #f9b23c;
    --glow: #fde3b8;
  }
  * { box-sizing: border-box; margin: 0; padding: 0; }
  html, body { width: 1200px; height: 869px; overflow: hidden; }
  body {
    background: var(--bg);
    font-family: "Arimo", Arial, sans-serif;
    color: var(--ink);
    position: relative;
  }
  .sheet, .envelope, .card {
    position: absolute;
    background: var(--paper);
    overflow: hidden;
  }
  .sheet { width: 310px; height: 438px; top: 40px; }
  .sheet--fax { left: 60px; }
  .sheet--letter { left: 410px; }
  .envelope { left: 60px; top: 530px; width: 600px; height: 290px; }
  .card { width: 380px; height: 218px; border-radius: 12px; left: 760px; }
  .card--front { top: 150px; }
  .card--back { top: 420px; }

  .brand { position: absolute; display: flex; align-items: center; gap: 6px; }
  .brand__dot { width: 20px; height: 20px; border-radius: 50%; background: var(--orange); flex: none; }
  .brand__name {
    font-family: "Tinos", "Times New Roman", serif;
    font-weight: 700; color: var(--ink);
    font-size: 11px; line-height: 1.05; letter-spacing: 0.3px;
  }
  .brand--lg .brand__dot { width: 30px; height: 30px; }
  .brand--lg .brand__name { font-size: 15px; }

  .glow { position: absolute; border-radius: 50%;
    background: radial-gradient(circle, var(--glow) 0%, rgba(253,227,184,0.35) 45%, rgba(255,255,255,0) 70%); }

  .contact { position: absolute; font-size: 6px; line-height: 1.6; color: var(--muted); }
  .contact li { list-style: none; display: flex; align-items: center; gap: 4px; }
  .contact li::before { content: ""; width: 4px; height: 4px; background: var(--orange); }

  .fax-title { position: absolute; right: 24px; top: 118px; font-weight: 700; font-size: 13px; }
  .fax-table { position: absolute; left: 22px; top: 68px; width: 266px; border-collapse: collapse; font-size: 6px; }
  .fax-table td { border: 1px solid var(--ink); height: 13px; padding: 0 3px; }
  .fax-table .label { width: 34px; }
  .fax-options { position: absolute; left: 22px; top: 170px; display: flex; gap: 10px; font-size: 6px; }
  .fax-options span::before { content: ""; display: inline-block; width: 5px; height: 5px; border: 1px solid var(--ink); margin-right: 2px; vertical-align: -1px; }

  .envelope__flap { position: absolute; inset: 0; }
  .envelope__window { position: absolute; left: 40px; top: 200px; width: 200px; height: 52px; background: #ececec; border: 1px solid #d8d8d8; }

  .card__person { position: absolute; left: 22px; top: 74px; }
  .card__name { font-size: 11px; font-weight: 700; color: var(--orange-deep); }
  .card__role { font-size: 8px; color: var(--muted); margin-top: 2px; }
  .card--front .contact { left: 22px; top: 112px; font-size: 7.5px; }
  .card--front .contact li::before { width: 5px; height: 5px; }
  .card__art { position: absolute; right: 0; top: 0; width: 150px; height: 100%;
    background: radial-gradient(circle at 100% 55%, var(--orange-light) 0%, var(--orange) 45%, var(--orange-deep) 75%, rgba(233,101,12,0) 76%); }
  .card--back { background: linear-gradient(135deg, var(--orange-deep) 0%, var(--orange) 50%, var(--orange-light) 100%); }
  .card--back .card__art { width: 100%; background: radial-gradient(circle at 78% 60%, rgba(255,240,200,0.7) 0%, rgba(255,220,140,0.25) 35%, rgba(255,255,255,0) 60%); }
</style>
</head>
<body>

  <section class="sheet sheet--fax" aria-label="Fax cover sheet">
    <div class="brand" style="left:22px;top:22px">
      <span class="brand__dot"></span>
      <span class="brand__name">BLUECREST<br>Mobile Ultrasound</span>
    </div>
    <ul class="contact" style="right:22px;top:24px">
      <li>1200 Harbor Lane, Hollywood, FL 33021</li>
      <li>(954) 555-0142</li>
      <li>info@bluecrestmobileultrasound.example</li>
    </ul>
    <table class="fax-table">
      <tr><td class="label">To</td><td></td><td class="label">From</td><td></td></tr>
      <tr><td class="label">Fax</td><td></td><td class="label">Phone</td><td></td></tr>
      <tr><td class="label">Re</td><td></td><td class="label">Date</td><td></td></tr>
      <tr><td class="label">Pages</td><td></td><td class="label">CC</td><td></td></tr>
    </table>
    <div class="fax-title">FAX</div>
    <div class="fax-options">
      <span>Urgent</span><span>For Review</span><span>Please Comment</span><span>Please Reply</span><span>Please Recycle</span>
    </div>
    <div class="glow" role="img" aria-label="Soft orange glow decoration" style="width:260px;height:260px;right:-70px;bottom:-60px"></div>
  </section>

  <section class="sheet sheet--letter" aria-label="Letterhead">
    <div class="brand" style="left:22px;top:22px">
      <span class="brand__dot"></span>
      <span class="brand__name">BLUECREST<br>Mobile Ultrasound</span>
    </div>
    <ul class="contact" style="right:22px;top:24px">
      <li>1200 Harbor Lane, Hollywood, FL 33021</li>
      <li>(954) 555-0142</li>
      <li>www.bluecrestmobileultrasound.example</li>
    </ul>
    <div class="glow" role="img" aria-label="Soft orange glow decoration" style="width:280px;height:280px;right:-80px;bottom:-70px"></div>
  </section>

  <section class="envelope" aria-label="Envelope">
    <svg class="envelope__flap" viewBox="0 0 600 290" preserveAspectRatio="none" aria-hidden="true">
      <polyline points="0,0 300,140 600,0" fill="none" stroke="#e2e2e2" stroke-width="1.5"/>
    </svg>
    <div class="brand" style="left:40px;top:110px">
      <span class="brand__dot"></span>
      <span class="brand__name">BLUECREST<br>Mobile Ultrasound</span>
    </div>
    <ul class="contact" style="left:40px;top:150px">
      <li>1200 Harbor Lane, Hollywood, FL 33021</li>
      <li>www.bluecrestmobileultrasound.example</li>
    </ul>
    <div class="envelope__window"></div>
    <div class="glow" role="img" aria-label="Soft orange glow decoration" style="width:300px;height:300px;right:-60px;bottom:-120px"></div>
  </section>

  <section class="card card--front" aria-label="Business card front">
    <div class="brand brand--lg" style="left:22px;top:22px">
      <span class="brand__dot"></span>
      <span class="brand__name">BLUECREST<br>Mobile Ultrasound</span>
    </div>
    <div class="card__person">
      <div class="card__name">Dana Whitcombe, RDMS, RVT</div>
      <div class="card__role">President/Owner</div>
    </div>
    <ul class="contact">
      <li>1200 Harbor Lane, Hollywood, FL 33021</li>
      <li>(954) 555-0142</li>
      <li>info@bluecrestmobileultrasound.example</li>
      <li>www.bluecrestmobileultrasound.example</li>
    </ul>
    <div class="card__art" role="img" aria-label="Bright orange gradient decoration"></div>
  </section>

  <section class="card card--back" aria-label="Business card back">
    <div class="card__art" role="img" aria-label="Warm light glow over orange gradient"></div>
  </section>

</body>
</html>
```